SkyvornQ Business Cards and Stationary Design

Need a design for our business cards and stationary. I want to carry on the theme of the logo. I want the business cards to have a design on the back. I would like the business cards and the stationary to carry the same theme, design scheme, and branding

Target Market(s)

Airlines and Maintenance Facilities

Industry/Entity Type

Aviation

Contact Information for Business Card

Name
Position Title
Address: 4827 Trellis Hollow Road, Fort Pierce, Florida, 34951
Office Number
Mobile Number
Email
Website

Font styles to use
Serif
Sans Serif

Colors

Designer to choose colors to be used in the design.

```html
<!DOCTYPE html>
<html lang="en">
<head>
<meta charset="utf-8">
<title>SkyvornQ Business Card</title>
<link rel="stylesheet" href="https://fonts.googleapis.com/css2?family=Exo+2:wght@500&family=Roboto:wght@400;500&display=swap">
<style>
  :root {
    --navy: #0c2a57;
    --navy-deep: #081f44;
    --navy-light: #1a3d72;
    --white: #ffffff;
    --paper: #f6f7f8;
    --ink: #0f2b55;
    --stage: #e7e9ec;
  }
  * { margin: 0; padding: 0; box-sizing: border-box; }
  html, body {
    width: 1200px; height: 950px; overflow: hidden;
    background: var(--stage);
  }
  .sheet {
    width: 1200px; height: 950px;
    display: flex; align-items: center; justify-content: center;
    gap: 48px;
  }
  .card {
    width: 540px; height: 310px;
    border-radius: 22px;
    position: relative;
    box-shadow: 0 8px 24px rgba(8, 31, 68, 0.18);
    overflow: hidden;
  }
  .card--front {
    background: linear-gradient(140deg, var(--navy-light) 0%, var(--navy) 45%, var(--navy-deep) 100%);
    color: var(--white);
  }
  .card--back { background: var(--paper); }

  .front-mark {
    position: absolute; top: 38px; right: 44px;
    font-family: "Roboto", sans-serif; font-weight: 500;
    font-size: 26px; color: var(--white);
  }
  .contact {
    position: absolute; left: 40px; bottom: 34px;
    font-family: "Roboto", sans-serif;
  }
  .contact__name {
    font-family: "Exo 2", sans-serif; font-weight: 500;
    font-size: 22px; letter-spacing: 4px; text-transform: uppercase;
  }
  .contact__title {
    font-size: 12px; letter-spacing: 2.5px; text-transform: uppercase;
    margin: 2px 0 12px; opacity: 0.9;
  }
  .contact__address { font-size: 12.5px; line-height: 1.45; margin-bottom: 8px; }
  .contact__list { list-style: none; font-size: 12.5px; line-height: 1.6; }
  .contact__list li { display: flex; align-items: center; gap: 9px; }
  .contact__list svg { width: 12px; height: 12px; flex: none; }

  .brand {
    position: absolute; inset: 0;
    display: flex; align-items: center; justify-content: center;
  }
  .brand__name {
    font-family: "Roboto", sans-serif; font-weight: 500;
    font-size: 40px; letter-spacing: 2px; color: var(--ink);
  }
</style>
</head>
<body>
<main class="sheet">
  <section class="card card--front">
    <div class="front-mark">SkyvornQ</div>
    <div class="contact">
      <p class="contact__name">Dorian Kessell</p>
      <p class="contact__title">CEO/Founder</p>
      <p class="contact__address">4827 Trellis Hollow Road<br>Fort Pierce, Florida, 34951</p>
      <ul class="contact__list">
        <li><svg viewBox="0 0 12 12" fill="#fff"><path d="M2.5 0.8 4.3 3 3.4 4.3c.7 1.6 2.2 3.1 3.8 3.8l1.3-.9 2.2 1.8-1 1.9C5.4 11 .9 6.5 .6 2z"/></svg>689 512 7740</li>
        <li><svg viewBox="0 0 12 12" fill="none" stroke="#fff" stroke-width="1.2"><rect x="3" y="0.8" width="6" height="10.4" rx="1"/><line x1="5" y1="9.5" x2="7" y2="9.5"/></svg>836 205 4481</li>
        <li><svg viewBox="0 0 12 12" fill="none" stroke="#fff" stroke-width="1.2"><rect x="0.8" y="2.5" width="10.4" height="7" rx="0.8"/><path d="M1 3 6 7 11 3"/></svg>info@skyvornq.com</li>
        <li><svg viewBox="0 0 12 12" fill="none" stroke="#fff" stroke-width="1.1"><circle cx="6" cy="6" r="5.2"/><ellipse cx="6" cy="6" rx="2.2" ry="5.2"/><line x1="0.8" y1="6" x2="11.2" y2="6"/></svg>www.skyvornq.com</li>
      </ul>
    </div>
  </section>

  <section class="card card--back">
    <div class="brand">
      <span class="brand__name">SkyvornQ</span>
    </div>
  </section>
</main>
</body>
</html>
```